SaaS Early tech startup business card design

Unique design for experience ecommerce platform company. the business cards will be used by executive members. conformance with color code is required.

```html
<!DOCTYPE html>
<html lang="en">
<head>
<meta charset="UTF-8">
<title>Nuvra Business Card</title>
<link href="https://fonts.googleapis.com/css2?family=Arimo:wght@400;700&display=swap" rel="stylesheet">
<style>
  :root {
    --navy: #23253f;
    --navy-deep: #1d1f36;
    --teal: #2bbf9c;
    --blue: #1b6f9c;
    --white: #ffffff;
    --grey-text: #6f7178;
    --stage: #2b2b2e;
  }
  * { margin: 0; padding: 0; box-sizing: border-box; }
  html, body {
    width: 1200px; height: 900px; overflow: hidden;
    background: var(--stage);
    font-family: "Arimo", Arial, sans-serif;
  }
  .canvas { position: relative; width: 1200px; height: 900px; }

  .card {
    position: absolute; left: 285px; width: 630px; height: 360px;
    border-radius: 22px; overflow: hidden;
    box-shadow: 0 14px 30px rgba(0,0,0,.45);
  }

  /* front */
  .card-front { top: 50px; background: var(--navy); }
  .card-front .brand {
    position: absolute; right: 150px; top: 40px;
    font-size: 64px; font-weight: 700; color: var(--teal); letter-spacing: 1px;
  }
  .card-front .decor {
    position: absolute; right: 20px; top: 110px; width: 200px; height: 150px;
    border-radius: 50%;
    background: radial-gradient(ellipse at center, rgba(43,191,156,.35), rgba(27,111,156,.15) 60%, transparent 72%);
  }
  .card-front .stat {
    position: absolute; left: 50px; top: 150px; color: var(--white);
  }
  .stat-figure { font-size: 60px; color: var(--teal); line-height: 1; }
  .stat-text { font-size: 21px; line-height: 1.3; margin-top: 8px; }
  .front-band {
    position: absolute; left: 0; right: 0; bottom: 0; height: 20px;
    background: linear-gradient(90deg, var(--blue), var(--teal));
  }

  /* back */
  .card-back { top: 490px; background: var(--white); }
  .card-back .brand {
    position: absolute; right: 50px; top: 40px;
    font-size: 64px; font-weight: 700; color: var(--teal); letter-spacing: 1px;
  }
  .identity {
    position: absolute; left: 40px; top: 140px;
    padding-left: 14px; border-left: 6px solid var(--teal);
  }
  .identity .name { font-size: 28px; font-weight: 700; color: var(--teal); }
  .identity .role { font-size: 19px; color: var(--grey-text); margin-top: 4px; }
  .back-band {
    position: absolute; left: 0; right: 0; top: 218px; height: 8px;
    background: linear-gradient(90deg, var(--blue) 45%, var(--teal) 55%);
  }
  .back-footer {
    position: absolute; left: 0; right: 0; top: 226px; bottom: 0;
    background: var(--navy-deep);
    display: flex; justify-content: space-between; align-items: center;
    padding: 0 40px;
  }
  .contact-list { list-style: none; color: var(--white); font-size: 20px; }
  .contact-list li { display: flex; align-items: center; gap: 12px; margin: 5px 0; }
  .contact-icon { width: 24px; height: 24px; }
  .address { color: var(--white); font-size: 20px; text-align: right; line-height: 1.35; }
</style>
</head>
<body>
<div class="canvas">

  <section class="card card-front">
    <div class="brand">Nuvra</div>
    <div class="decor" role="img" aria-label="Abstract looping line pattern in teal and blue"></div>
    <div class="stat">
      <div class="stat-figure">63%</div>
      <div class="stat-text">Of Consumer Value<br>Privacy Over Popularity<br>When Dealing With<br>Online Platfrom</div>
    </div>
    <div class="front-band"></div>
  </section>

  <section class="card card-back">
    <div class="brand">Nuvra</div>
    <div class="identity">
      <div class="name">Jonathan Smith</div>
      <div class="role">Manager</div>
    </div>
    <div class="back-band"></div>
    <div class="back-footer">
      <ul class="contact-list">
        <li>
          <svg class="contact-icon" viewBox="0 0 24 24"><rect width="24" height="24" rx="5" fill="#2bbf9c"/><path d="M8 6c-1 1-1.5 2-.8 3.8 1 2.6 3.4 5 6 6 1.8.7 2.8.2 3.8-.8l-2-2-1.5 1c-1.5-.7-2.8-2-3.5-3.5l1-1.5z" fill="#fff"/></svg>
          123-456-2100
        </li>
        <li>
          <svg class="contact-icon" viewBox="0 0 24 24"><rect width="24" height="24" rx="5" fill="#2bbf9c"/><rect x="5" y="7" width="14" height="10" fill="none" stroke="#fff" stroke-width="1.6"/><path d="M5 7l7 6 7-6" fill="none" stroke="#fff" stroke-width="1.6"/></svg>
          youremail@mailbox.com
        </li>
        <li>
          <svg class="contact-icon" viewBox="0 0 24 24"><rect width="24" height="24" rx="5" fill="#2bbf9c"/><circle cx="12" cy="12" r="6.5" fill="none" stroke="#fff" stroke-width="1.6"/><path d="M5.5 12h13M12 5.5c-3 3.5-3 9.5 0 13M12 5.5c3 3.5 3 9.5 0 13" fill="none" stroke="#fff" stroke-width="1.3"/></svg>
          www.yourwebsite.com
        </li>
      </ul>
      <div class="address">Your address, city<br>state, ZIP 0000</div>
    </div>
  </section>

</div>
</body>
</html>
```